Stage Design Company Business Card

We are looking to step up up our business card design for our team.

We are a Full service Design and Consultation company for Stage and TV with an emphasis in Theatrical Lighting.

We like our materials to be clean and modern with solid colors free of patterns and gradients. Our brand consists of 4 primary colors Purple, Black, Grey, and White. Provided is our Word Mark as well as our Symbol Logo.

We would like our cards to leave an impression beyond the information, show our attention to design and detail, and make our marks an easily recognized feature (together or apart) for our clients.

We need a warm approachable comfortable feel for some clients, and a professional flair for the board member type clients.

Attached are our brand elements, and our existing cards to give a sense of our style and a glipse at the information we provide on our cards.

Target Market(s)

broad client base from church leaders to high school teachers and architects.

Industry/Entity Type

Business

Contact Information for Business Card

We format our phone number with periods not parenthesis or dashes. Information will be edited for each of our team members, and team member specific cards are not part of this scope, but rather a template so to speak.

Font styles to use
Sans Serif

Colors
6b449b
ffffff
000000
333333
aaaaaa

Requirements
Must have
• Wordmark and logo mark present (does not need to exist on the same side of card)
• Brand Colors,
• Name, Phone, Email, Address.
• Unique choices that make someone stop and take a second look
Nice to have
• It would be nice to somehow convey what we DO, as our brand name does not lend itself to this, outside of an obvious tagline though.....
• social media if not crowded. all of our handles match (instagram, twitter, facebook)
Should not have
• "clipart"

```html
<!DOCTYPE html>
<html lang="en">
<head>
<meta charset="utf-8">
<title>Halvern Stageworks — Business Card</title>
<link href="https://fonts.googleapis.com/css2?family=Jost:wght@400;500;600&display=swap" rel="stylesheet">
<style>
  :root {
    --backdrop: #1b1b1b;
    --card: #262626;
    --ink: #ffffff;
    --ink-soft: #e6e6e6;
    --muted: #aaaaaa;
    --accent: #4a3390;
    --accent-line: #5a3e9a;
  }
  * { box-sizing: border-box; margin: 0; padding: 0; }
  html, body {
    width: 1200px; height: 900px; overflow: hidden;
    background: var(--backdrop);
    font-family: "Jost", "Helvetica Neue", Arial, sans-serif;
    color: var(--ink);
  }
  .canvas {
    width: 1200px; height: 900px;
    display: flex; flex-direction: column;
    align-items: center; justify-content: center; gap: 40px;
  }
  .card {
    position: relative;
    width: 600px; height: 343px;
    background: var(--card);
    box-shadow: 0 14px 30px rgba(0,0,0,0.45);
    overflow: hidden;
  }
  /* Front */
  .card--front {
    display: flex; flex-direction: column;
    align-items: center; justify-content: center; gap: 22px;
  }
  .brand-dot {
    width: 74px; height: 74px;
    border: 3px solid var(--ink);
    border-radius: 50%;
  }
  .brand-name {
    font-weight: 500;
    font-size: 22px;
    letter-spacing: 0.32em;
    color: var(--ink);
    padding-left: 0.32em;
  }
  /* Back */
  .identity {
    position: absolute;
    top: 118px; right: 336px;
    text-align: right;
  }
  .identity__name {
    font-weight: 600;
    font-size: 24px;
    letter-spacing: 0.04em;
    line-height: 1.1;
  }
  .identity__role {
    font-weight: 400;
    font-size: 17px;
    color: var(--ink-soft);
    margin-top: 6px;
  }
  .divider {
    position: absolute;
    top: 126px; left: 282px;
    width: 2px; height: 62px;
    background: var(--accent-line);
  }
  .contacts {
    position: absolute;
    top: 124px; left: 302px;
    list-style: none;
    font-size: 16px;
    letter-spacing: 0.06em;
    line-height: 21px;
  }
  .contacts li { display: flex; align-items: center; gap: 12px; }
  .contacts svg { width: 12px; height: 12px; flex: none; }
  .address {
    position: absolute;
    left: 150px; bottom: 40px;
    font-size: 16px;
    letter-spacing: 0.06em;
  }
  .accent-band {
    position: absolute;
    left: 0; right: 0; bottom: 0;
    height: 12px;
    background: var(--accent);
  }
</style>
</head>
<body>
<main class="canvas">
  <section class="card card--front" aria-label="Card front">
    <div class="brand-dot" aria-hidden="true"></div>
    <div class="brand-name">HALVERN STAGEWORKS</div>
  </section>

  <section class="card card--back" aria-label="Card back">
    <div class="identity">
      <div class="identity__name">MARCUS T ELDEN</div>
      <div class="identity__role">Owner</div>
    </div>
    <div class="divider" aria-hidden="true"></div>
    <ul class="contacts">
      <li>
        <svg viewBox="0 0 12 12" aria-hidden="true"><rect x="3" y="0.8" width="6" height="10.4" rx="1" fill="none" stroke="#fff" stroke-width="1.3"/><line x1="5" y1="9.3" x2="7" y2="9.3" stroke="#fff" stroke-width="1"/></svg>
        <span>800.555.0142</span>
      </li>
      <li>
        <svg viewBox="0 0 12 12" aria-hidden="true"><rect x="0.5" y="2.5" width="11" height="7.5" fill="#fff"/><polyline points="0.5,2.8 6,7 11.5,2.8" fill="none" stroke="#262626" stroke-width="1.2"/></svg>
        <span>hello@halvern-s.com</span>
      </li>
      <li>
        <svg viewBox="0 0 12 12" aria-hidden="true"><circle cx="5" cy="5" r="3.6" fill="none" stroke="#fff" stroke-width="1.6"/><line x1="7.6" y1="7.6" x2="11" y2="11" stroke="#fff" stroke-width="1.8" stroke-linecap="round"/></svg>
        <span>halvern-s.com</span>
      </li>
    </ul>
    <div class="address">112 E. Oak ST Tempe, AZ 85281</div>
    <div class="accent-band" aria-hidden="true"></div>
  </section>
</main>
</body>
</html>
```